Exclusive beauty salon needs a price list or services booklet

I need a new very attractive flyer for my beauty salon, containing information on the different services and their prices.
In attachment you can find a pdf of the "old" one, but I'd love to have a beautifully designed new one!
I'd love to have a booklet in format 148 x 148 mm, or in US format, containing 12 or 16 pages, but if you can offer other nice looking designs they are welcome!
The services that need to come in the booklet with their prices can all be found on my website: www.atelierverano.be, starting with
Gelaatsverzorging
Wimperverlenging
Suikerontharing
Wimperlifting
Permanente Make Up
Airbrush Tanning

Target Market(s)

woman from 20 to 89 years old

Industry/Entity Type

Beauty Salon

Font styles to use
Sans Serif

Colors

Designer to choose colors to be used in the design.

Requirements
Must have
• a classy nice look, it must contain details about the services from my beauty salon and their prices, and nice pictures.
• The Names, prices and explanations of the services can easily be found on my website: www.atelierverano.be
Nice to have
• In attachment you can find the "old" price list in pdf, what I need now is a "new booklet" with the new logo and updated services price list.
• I need a very nice and attractive looking booklet, classy chique, Paris chique, looking very expensive.
Should not have
• Not too much colors, not too curly, but still feminine

```html
<!DOCTYPE html>
<html lang="nl">
<head>
<meta charset="utf-8">
<title>Atelier Verano – Prijsbrochure</title>
<link href="https://fonts.googleapis.com/css2?family=Montserrat:wght@300;400&family=Open+Sans:wght@400&display=swap" rel="stylesheet">
<style>
  :root {
    --backdrop: #b4d4d6;
    --paper: #efedea;
    --panel: #e8e5e1;
    --teal-light: #88c6c8;
    --teal-deep: #539e9f;
    --ink: #6f6f6f;
    --ink-soft: #9a9a9a;
    --accent: #5fb0b3;
    --skin-light: #f3e6e2;
    --skin-deep: #e2bcb6;
  }
  * { box-sizing: border-box; margin: 0; padding: 0; }
  html, body { width: 1200px; height: 700px; overflow: hidden; }
  body {
    background: var(--backdrop);
    font-family: "Montserrat", sans-serif;
    color: var(--ink);
    position: relative;
  }
  .spread {
    position: absolute;
    left: 60px; top: 100px;
    width: 1080px; height: 500px;
    display: flex;
  }
  .page {
    width: 540px; height: 500px;
    background: var(--paper);
    position: relative;
  }
  /* back cover */
  .back-cover { padding: 18px; }
  .back-cover__field {
    width: 100%; height: 100%;
    background: linear-gradient(90deg, var(--teal-light), var(--teal-deep));
    display: flex; align-items: center;
  }
  .contact-strip {
    width: 100%; height: 104px;
    margin-left: 40px; margin-right: 40px;
    background: var(--paper);
    display: flex; align-items: center;
  }
  .brand {
    flex: 0 0 210px;
    display: flex; flex-direction: column; align-items: center;
    gap: 6px;
  }
  .brand__name {
    font-weight: 300;
    font-size: 15px;
    letter-spacing: 5px;
    text-transform: uppercase;
    color: var(--ink);
  }
  .brand__tagline {
    font-weight: 300;
    font-size: 6px;
    letter-spacing: 2.5px;
    text-transform: uppercase;
    color: var(--ink-soft);
  }
  .contact-strip__divider {
    width: 1px; height: 62px; background: var(--ink-soft);
  }
  .contact {
    padding-left: 22px;
    font-family: "Open Sans", sans-serif;
    font-size: 8.5px;
    line-height: 1.45;
    color: var(--ink);
    list-style: none;
  }
  .contact__note { font-size: 6px; color: var(--ink-soft); }
  /* front cover */
  .front-cover { display: flex; }
  .front-cover__photo {
    width: 380px; height: 420px;
    margin-top: 18px;
    background: radial-gradient(ellipse at 60% 55%, var(--skin-deep), var(--skin-light) 70%, #f8f6f5);
  }
  .front-cover__panel {
    flex: 1;
    display: flex; flex-direction: column; align-items: center;
    padding-top: 80px;
  }
  .front-cover__url {
    position: absolute;
    right: 24px; bottom: 30px;
    font-size: 7px;
    letter-spacing: 2px;
    color: var(--ink-soft);
  }
  .front-cover__tab {
    position: absolute;
    right: 0; bottom: 32px;
    width: 12px; height: 5px;
    background: var(--accent);
  }
</style>
</head>
<body>
  <main class="spread">
    <section class="page back-cover">
      <div class="back-cover__field">
        <div class="contact-strip">
          <div class="brand">
            <span class="brand__name">Atelier Verano</span>
            <span class="brand__tagline">Schoonheidsinstituut</span>
          </div>
          <span class="contact-strip__divider"></span>
          <ul class="contact">
            <li>Atelier Verano Schoonheidsinstituut</li>
            <li>Lindenlaan 14 <span class="contact__note">nabij het stadspark</span></li>
            <li>9000 GENT</li>
            <li>0470 00 12 34</li>
            <li>info@atelierverano.be</li>
            <li>www.atelierverano.be</li>
          </ul>
        </div>
      </div>
    </section>
    <section class="page front-cover">
      <div class="front-cover__photo" role="img" aria-label="Close-up beauty portrait with soft skin tones"></div>
      <div class="front-cover__panel">
        <div class="brand">
          <span class="brand__name">Atelier Verano</span>
          <span class="brand__tagline">Schoonheidsinstituut</span>
        </div>
      </div>
      <span class="front-cover__url">www.atelierverano.be</span>
      <span class="front-cover__tab"></span>
    </section>
  </main>
</body>
</html>
```